Floor Inspections and Consulting

We provide inspections and consulting services on various floor coverings, e.g. carpet, hardwood, etc. We also do expert witness work for attorneys due to floor covering failures. We current have a logo, just need it incorporated into a new design. I have examples of cards I have found on the internet that capture my attention and make a statement. I have included our original business card, which in my opinion is terrible, but it does have our logo on it.

```html
<!DOCTYPE html>
<html lang="en">
<head>
<meta charset="utf-8">
<title>Groundline Floor Inspections – Business Card</title>
<link rel="stylesheet" href="https://fonts.googleapis.com/css2?family=Archivo:wght@800&family=Arimo:wght@400;700&display=swap">
<style>
  :root {
    --backdrop: #3a3a3c;
    --card: #1b1b1c;
    --card-edge: #0e0e0f;
    --accent: #f0960f;
    --accent-dark: #b86e05;
    --ink-light: #ffffff;
  }
  * { margin: 0; padding: 0; box-sizing: border-box; }
  html, body {
    width: 1200px; height: 1015px; overflow: hidden;
    background: var(--backdrop);
  }
  .canvas { position: relative; width: 1200px; height: 1015px; }

  .card {
    position: absolute; left: 220px;
    width: 760px; height: 434px;
    background: var(--card);
    border-radius: 26px;
    box-shadow: 0 6px 0 var(--card-edge), 0 18px 40px rgba(0,0,0,.45);
    overflow: hidden;
  }
  .card--front { top: 40px; }
  .card--back { top: 530px; }

  /* brand lockup */
  .brand { display: flex; align-items: center; gap: 16px; }
  .brand__mark { width: 38px; height: 38px; background: var(--accent); flex: none; }
  .brand__name {
    font-family: "Archivo", sans-serif; font-weight: 800;
    color: var(--accent); text-transform: uppercase;
    line-height: 1.02; letter-spacing: .5px;
  }

  /* front */
  .card--front .brand {
    position: absolute; left: 0; right: 0; top: 120px; justify-content: center;
  }
  .card--front .brand__mark { width: 58px; height: 58px; }
  .card--front .brand__name { font-size: 36px; }
  .tagline {
    position: absolute; left: 0; right: 0; top: 270px; text-align: center;
    font-family: "Arimo", sans-serif; font-weight: 700;
    font-size: 20px; letter-spacing: .5px; color: var(--ink-light);
    text-transform: uppercase;
  }
  .tagline-rule {
    position: absolute; left: 250px; right: 250px; top: 248px;
    height: 2px; background: var(--accent);
  }

  /* back */
  .name-ribbon {
    position: absolute; right: 0; top: 78px;
    width: 360px; height: 74px; background: var(--accent);
    display: flex; align-items: center; padding-left: 34px;
    font-family: "Archivo", sans-serif; font-weight: 800;
    font-size: 30px; color: var(--ink-light); letter-spacing: .5px;
    text-transform: uppercase;
  }
  .ribbon-fold {
    position: absolute; right: 270px; top: 152px; width: 40px; height: 14px;
  }
  .card--back .brand { position: absolute; left: 62px; top: 128px; }
  .card--back .brand__name { font-size: 24px; }

  .contacts { position: absolute; left: 0; top: 250px; list-style: none; }
  .contact {
    position: relative; height: 50px; display: flex; align-items: center;
    margin-bottom: 6px;
  }
  .contact__band { height: 40px; background: var(--accent); }
  .contact:nth-child(1) .contact__band { width: 118px; }
  .contact:nth-child(2) .contact__band { width: 150px; }
  .contact:nth-child(3) .contact__band { width: 182px; }
  .contact__icon { width: 50px; height: 50px; margin-left: -6px; flex: none; }
  .contact__text {
    font-family: "Arimo", sans-serif; font-size: 27px;
    color: var(--ink-light); margin-left: 18px; white-space: nowrap;
  }
</style>
</head>
<body>
<main class="canvas">

  <section class="card card--front" aria-label="Card front">
    <div class="brand">
      <span class="brand__mark"></span>
      <span class="brand__name">Groundline Floor<br>Inspections</span>
    </div>
    <div class="tagline-rule"></div>
    <p class="tagline">Certified floor covering inspection &amp; consulting</p>
  </section>

  <section class="card card--back" aria-label="Card back">
    <div class="name-ribbon">Daniel Verhoek</div>
    <svg class="ribbon-fold" viewBox="0 0 40 14"><polygon points="0,0 40,0 40,14" fill="var(--accent-dark)"/></svg>

    <div class="brand">
      <span class="brand__mark"></span>
      <span class="brand__name">Groundline Floor<br>Inspections</span>
    </div>

    <ul class="contacts">
      <li class="contact">
        <span class="contact__band"></span>
        <svg class="contact__icon" viewBox="0 0 50 50" aria-hidden="true">
          <polygon points="25,2 45,13.5 45,36.5 25,48 5,36.5 5,13.5" fill="var(--accent)" stroke="var(--card)" stroke-width="3"/>
          <path d="M18 16c-2 2-2 5 1 10s6 8 9 8c2 0 3-1 4-2l-4-4-2 2c-2-1-4-3-5-5l2-2-4-4z" fill="var(--card)"/>
        </svg>
        <span class="contact__text">303-555-0142</span>
      </li>
      <li class="contact">
        <span class="contact__band"></span>
        <svg class="contact__icon" viewBox="0 0 50 50" aria-hidden="true">
          <polygon points="25,2 45,13.5 45,36.5 25,48 5,36.5 5,13.5" fill="var(--accent)" stroke="var(--card)" stroke-width="3"/>
          <rect x="14" y="17" width="22" height="16" fill="none" stroke="var(--card)" stroke-width="2.5"/>
          <polyline points="14,17 25,27 36,17" fill="none" stroke="var(--card)" stroke-width="2.5"/>
        </svg>
        <span class="contact__text">daniel@groundlinefloors.com</span>
      </li>
      <li class="contact">
        <span class="contact__band"></span>
        <svg class="contact__icon" viewBox="0 0 50 50" aria-hidden="true">
          <polygon points="25,2 45,13.5 45,36.5 25,48 5,36.5 5,13.5" fill="var(--accent)" stroke="var(--card)" stroke-width="3"/>
          <g fill="none" stroke="var(--card)" stroke-width="2">
            <circle cx="25" cy="25" r="11"/>
            <ellipse cx="25" cy="25" rx="5" ry="11"/>
            <line x1="14" y1="25" x2="36" y2="25"/>
            <line x1="16" y1="19" x2="34" y2="19"/>
            <line x1="16" y1="31" x2="34" y2="31"/>
          </g>
        </svg>
        <span class="contact__text">www.groundlinefloors.com</span>
      </li>
    </ul>
  </section>

</main>
</body>
</html>
```